TA BRAMLEY BUSINESS CARD DESIGN PROJECT

We need to utilize our logo that was expertly created on PixelHarbor and now need to match this with a business card design.

```html
<!DOCTYPE html>
<html lang="en">
<head>
<meta charset="utf-8">
<title>TA BRAMLEY Business Card</title>
<link rel="stylesheet" href="https://fonts.googleapis.com/css2?family=Montserrat:wght@400;500;700&display=swap">
<style>
  :root {
    --stage: #4a4a4c;
    --card-black: #141414;
    --card-white: #ffffff;
    --brand-blue: #0e55ad;
    --emboss: #2b2b2d;
    --text-light: #ffffff;
  }
  * { margin: 0; padding: 0; box-sizing: border-box; }
  html, body { width: 1200px; height: 689px; overflow: hidden; }
  body {
    background: var(--stage);
    font-family: "Montserrat", sans-serif;
    position: relative;
  }
  .card {
    position: absolute;
    top: 184px;
    width: 560px;
    height: 320px;
    border-radius: 24px;
    overflow: hidden;
  }
  .card-back { left: 20px; background: var(--card-black); }
  .card-front { left: 620px; background: var(--card-white); }

  .back-wordmark {
    position: absolute;
    inset: 0;
    display: flex;
    align-items: center;
    justify-content: center;
    font-weight: 700;
    font-size: 54px;
    letter-spacing: 6px;
    color: var(--emboss);
  }

  .front-wave { position: absolute; inset: 0; }

  .front-wordmark {
    position: absolute;
    top: 58px;
    right: 44px;
    font-weight: 700;
    font-size: 36px;
    letter-spacing: 4px;
    color: var(--brand-blue);
  }

  .contact {
    position: absolute;
    left: 42px;
    top: 186px;
    color: var(--text-light);
    font-size: 11px;
    line-height: 14px;
  }
  .contact-accent {
    position: absolute;
    left: 24px;
    top: 190px;
    width: 6px;
    height: 40px;
    background: var(--brand-blue);
  }
  .contact-name {
    color: var(--brand-blue);
    font-weight: 700;
    font-size: 16px;
    line-height: 20px;
    letter-spacing: 0.5px;
  }
  .contact-title { font-weight: 500; margin-bottom: 8px; }
  .contact-address { margin-bottom: 8px; }
  .contact-line { display: flex; align-items: center; gap: 7px; }
  .contact-line svg { width: 10px; height: 10px; fill: var(--brand-blue); flex: none; }
</style>
</head>
<body>

  <section class="card card-back" aria-label="Business card back">
    <div class="back-wordmark">TA BRAMLEY</div>
  </section>

  <section class="card card-front" aria-label="Business card front">
    <svg class="front-wave" viewBox="0 0 560 320" width="560" height="320" aria-hidden="true">
      <path d="M0 170 C160 186 320 140 450 128 C510 122 545 130 560 140 L560 320 L0 320 Z" fill="var(--card-black)"/>
      <path d="M0 166 C160 182 320 128 450 115 C510 109 545 118 560 128" fill="none" stroke="var(--brand-blue)" stroke-width="5"/>
    </svg>

    <div class="front-wordmark">TA BRAMLEY</div>

    <div class="contact-accent"></div>
    <div class="contact">
      <div class="contact-name">OWEN CALDER</div>
      <div class="contact-title">Managing Director</div>
      <div class="contact-address">Your address, City<br>State, Zip 1234</div>
      <div class="contact-line">
        <svg viewBox="0 0 10 10"><path d="M2 0h2l1 3-1.5 1a6 6 0 0 0 2.5 2.5L7 5l3 1v2a2 2 0 0 1-2 2A8 8 0 0 1 0 2a2 2 0 0 1 2-2z"/></svg>
        <span>123 456 789</span>
      </div>
      <div class="contact-line">
        <svg viewBox="0 0 10 10"><path d="M0 2h10v6H0z M0 2l5 3.5L10 2" /></svg>
        <span>info@yourmail.com</span>
      </div>
      <div class="contact-line">
        <svg viewBox="0 0 10 10"><circle cx="5" cy="5" r="5"/></svg>
        <span>www.yourwebsite.com</span>
      </div>
    </div>
  </section>

</body>
</html>
```